Flat bootstrap design for existing site

I'm looking for a modern flat design based around an existing logo. This has to be a custom design (no external templates), and implemented into a bootstrap framework.

The logo is attached as 2 versions - choose whichever you want, that flows better with whatever design you choose.

Added screenshots of the existing site (currently using the default bootstrap layouts). Please make your designs around those pages in the screenshots (i.e. the homepage only has the postal code input and the header). The active page has 3 screenshots, because I wanted to illustrate the other states that would be visible (in the table rows).

This is a moving/junk removal website, just for some context.

Here's some example websites (flat designs) that I like, just to give you an idea of what I'm after.

https://www.plimvora.com/
https://dacklow.com/
https://trevanu.com/
https://quobrintal.com/en/

Coding

Coded - Design and coding required

Number of Pages Required

5+ page

Colors

Designer to choose colors to be used in the design.

Requirements
Must have
• It must be a modern/simple flat design, that is built around the existing logo (attached).
• It has to be implemented using bootstrap.

```html
<!DOCTYPE html>
<html lang="en">
<head>
<meta charset="utf-8">
<title>Tovrik — Sign In</title>
<link rel="stylesheet" href="https://fonts.googleapis.com/css2?family=Nunito:wght@400;600;800&display=swap">
<style>
  :root {
    --sky-light: #4ccaf6;
    --sky: #3ec3f4;
    --sky-deep: #2bb9ee;
    --band: rgba(40, 150, 200, 0.12);
    --white: #ffffff;
    --title-blue: #2b86c5;
    --field-border: #d4d4d4;
    --placeholder: #4a4a4a;
    --button: #4bc8f5;
  }
  * { box-sizing: border-box; margin: 0; padding: 0; }
  html, body {
    width: 1200px;
    height: 624px;
    overflow: hidden;
    font-family: "Nunito", sans-serif;
  }
  .page {
    position: relative;
    width: 1200px;
    height: 624px;
    overflow: hidden;
  }
  .page-backdrop {
    position: absolute;
    inset: 0;
    background:
      linear-gradient(125deg, var(--sky-light) 0%, var(--sky) 35%, var(--sky-deep) 55%, var(--sky-light) 75%, var(--sky) 100%);
  }
  .page-backdrop-band {
    position: absolute;
    left: 0;
    right: 0;
    top: 328px;
    bottom: 0;
    background: var(--band);
  }
  .site-header {
    position: absolute;
    left: 0;
    top: 0;
    width: 100%;
    height: 100px;
  }
  .brand {
    position: absolute;
    left: 86px;
    top: 28px;
    display: flex;
    align-items: center;
    gap: 10px;
    color: var(--white);
    font-weight: 800;
    font-size: 38px;
    letter-spacing: 1px;
    line-height: 1;
  }
  .brand-dot {
    width: 26px;
    height: 26px;
    border-radius: 50%;
    background: var(--white);
  }
  .main-nav {
    position: absolute;
    top: 39px;
    left: 588px;
    display: flex;
    gap: 0;
    list-style: none;
  }
  .main-nav a {
    position: absolute;
    white-space: nowrap;
    color: var(--white);
    text-decoration: none;
    font-size: 15.5px;
    font-weight: 400;
  }
  .nav-book { left: 0; }
  .nav-how { left: 97px; }
  .nav-driver { left: 272px; }
  .nav-signin { left: 467px; }
  .signin-card {
    position: absolute;
    left: 366px;
    top: 182px;
    width: 469px;
    height: 341px;
    background: var(--white);
    border-radius: 6px;
    box-shadow: 0 6px 24px rgba(0, 80, 120, 0.12);
  }
  .signin-title {
    position: absolute;
    top: 42px;
    width: 100%;
    text-align: center;
    color: var(--title-blue);
    font-weight: 400;
    font-size: 31px;
    letter-spacing: 0.5px;
  }
  .signin-field,
  .signin-button {
    position: absolute;
    left: 59px;
    width: 351px;
    height: 44px;
    border-radius: 22px;
    display: flex;
    align-items: center;
    justify-content: center;
    font-family: "Nunito", sans-serif;
  }
  .signin-field {
    border: 1px solid var(--field-border);
    background: var(--white);
    box-shadow: 0 2px 3px rgba(0, 0, 0, 0.08);
    color: var(--placeholder);
    font-size: 13px;
  }
  .field-email { top: 117px; }
  .field-password { top: 174px; }
  .signin-button {
    top: 228px;
    border: none;
    background: var(--button);
    color: var(--white);
    font-size: 17px;
    box-shadow: 0 2px 5px rgba(0, 0, 0, 0.15);
  }
</style>
</head>
<body>
<div class="page">
  <div class="page-backdrop" role="img" aria-label="Low-poly faceted background in light sky-blue tones"></div>
  <div class="page-backdrop-band"></div>

  <header class="site-header">
    <div class="brand"><span class="brand-dot"></span>TOVRIK</div>
    <nav class="main-nav">
      <a class="nav-book" href="#">BOOK</a>
      <a class="nav-how" href="#">HOW IT WORKS</a>
      <a class="nav-driver" href="#">BECOME A DRIVER</a>
      <a class="nav-signin" href="#">SIGN IN</a>
    </nav>
  </header>

  <main class="signin-card">
    <h1 class="signin-title">PLEASE SIGN IN</h1>
    <div class="signin-field field-email">Email address</div>
    <div class="signin-field field-password">Password</div>
    <div class="signin-button">LOGIN</div>
  </main>
</div>
</body>
</html>
```